tinyTally Resource Book - 10 maths tasks to do outside

I need a 22 (11 pages back to back) page A6 sized book produced to standard for submission to professional printer. Needs to be as .pdf file showing guide lines and allowances for colour bleed. I have text already written and submitted as attachment in a Word file with margins set to A6 size. The theme of the materials is "Nature Play" so using lots of pictures from nature (Australia preferably) and showing lots of patterns in nature (rocks, leaves, flower petals etc). Some of the tasks refer to specific activities, such as "shadows" and "floating" so would be great to illustrate appropriately. The big emphasis is on learning outside the classroom, getting kids to engage actively with nature. I would like to see the pages as full colour - so not white background. The book itself will be spiral bound along the top edge so a margin of at least 1cm will be required at the top of each page (or the bottom of even numbered pages). Book will be printed on plastic laminated matte paper for outdoor use. Font size needs to be big enough to read. Fonts sizes, alignments and page numbers are all different at the moment and need to be standardised. One photo is included in a page as a sample if you can use it, otherwise disregard. Logo for Wattlebrook Numeracy Guild is also included to have as part of the acknowledgements at the back of the book.

Target Market(s)

Book is for early childhood and preschool teachers.

Industry/Entity Type

Education

Font styles to use
Sans Serif

Requirements
Must have
• Colour and appeal.
Nice to have
• Use of natural colours instead of bright catchy colours but that is your call.
Should not have
• American spelling

```html
<!DOCTYPE html>
<html lang="en-AU">
<head>
<meta charset="utf-8">
<title>Repeat My Pattern – tinyTally Resource Book</title>
<link rel="stylesheet" href="https://fonts.googleapis.com/css2?family=Jost:wght@400;500;800&display=swap">
<style>
  :root {
    --paper: #ffffff;
    --heading-blue: #2b3a8f;
    --body-ink: #2f2a28;
    --bullet-red: #d4202c;
    --leaf-red: #f3b6a8;
    --leaf-amber: #f8d9a6;
    --leaf-pale: #fbe7dc;
    --trim-line: #3a3a3a;
  }
  * { margin: 0; padding: 0; box-sizing: border-box; }
  html, body { width: 892px; height: 1200px; overflow: hidden; background: var(--paper); }
  .page {
    position: relative;
    width: 892px;
    height: 1200px;
    background: var(--paper);
    font-family: "Jost", sans-serif;
    color: var(--body-ink);
  }
  .trim-marks { position: absolute; inset: 0; }
  .leaf-backdrop {
    position: absolute;
    left: 52px; top: 52px;
    width: 788px; height: 1096px;
    background:
      radial-gradient(circle at 25% 15%, var(--leaf-red) 0, transparent 28%),
      radial-gradient(circle at 80% 20%, var(--leaf-red) 0, transparent 25%),
      radial-gradient(circle at 20% 55%, var(--leaf-amber) 0, transparent 26%),
      radial-gradient(circle at 75% 60%, var(--leaf-red) 0, transparent 30%),
      radial-gradient(circle at 40% 90%, var(--leaf-amber) 0, transparent 28%),
      var(--leaf-pale);
  }
  .task-title, .section-heading {
    position: absolute;
    left: 126px;
    color: var(--heading-blue);
    font-weight: 800;
    line-height: 1;
    letter-spacing: 0.5px;
  }
  .task-title { top: 147px; font-size: 50px; }
  .section-heading { font-size: 39px; }
  .bullet-list {
    position: absolute;
    left: 186px;
    list-style: none;
    font-size: 29px;
    font-weight: 400;
    line-height: 42px;
  }
  .bullet-list li { position: relative; padding-left: 32px; }
  .bullet-list li::before {
    content: "";
    position: absolute;
    left: 3px; top: 14px;
    width: 14px; height: 14px;
    background: var(--bullet-red);
    transform: rotate(45deg);
  }
  .task-steps { top: 201px; width: 560px; }
  .prompts-heading { top: 399px; }
  .prompts-list { top: 451px; width: 540px; }
  .variations-heading { top: 605px; }
  .variations-list { top: 657px; width: 540px; }
  .ideas-heading { top: 855px; }
  .ideas-list { top: 905px; width: 200px; }
  .pattern-row {
    position: absolute;
    border-radius: 6px;
    background: linear-gradient(90deg, #e0952c, #d9662a 30%, #8aa53a 50%, #e0952c 70%, #d9662a);
    opacity: 0.85;
  }
  .pattern-row-first { left: 376px; top: 876px; width: 392px; height: 68px; }
  .pattern-row-second { left: 392px; top: 980px; width: 392px; height: 68px; }
</style>
</head>
<body>
<div class="page">
  <div class="leaf-backdrop" role="img" aria-label="Faded photograph of scattered red and amber autumn leaves"></div>

  <svg class="trim-marks" width="892" height="1200" viewBox="0 0 892 1200" aria-hidden="true">
    <g stroke="var(--trim-line)" stroke-width="1" fill="none">
      <line x1="52" y1="0" x2="52" y2="36"/><line x1="0" y1="52" x2="36" y2="52"/>
      <line x1="74" y1="36" x2="74" y2="74"/><line x1="36" y1="74" x2="74" y2="74"/>
      <line x1="840" y1="0" x2="840" y2="36"/><line x1="856" y1="52" x2="892" y2="52"/>
      <line x1="818" y1="36" x2="818" y2="74"/><line x1="818" y1="74" x2="856" y2="74"/>
      <line x1="52" y1="1164" x2="52" y2="1200"/><line x1="0" y1="1148" x2="36" y2="1148"/>
      <line x1="74" y1="1126" x2="74" y2="1164"/><line x1="36" y1="1126" x2="74" y2="1126"/>
      <line x1="840" y1="1164" x2="840" y2="1200"/><line x1="856" y1="1148" x2="892" y2="1148"/>
      <line x1="818" y1="1126" x2="818" y2="1164"/><line x1="818" y1="1126" x2="856" y2="1126"/>
    </g>
  </svg>

  <h1 class="task-title">10. Repeat My Pattern</h1>
  <ul class="bullet-list task-steps">
    <li>Make a pattern from your choice of materials</li>
    <li>Ask partner to continue the pattern</li>
    <li>Swap roles with partner</li>
  </ul>

  <h2 class="section-heading prompts-heading">Prompting questions</h2>
  <ul class="bullet-list prompts-list">
    <li>Can you keep the same objects but introduce a new object into your pattern?</li>
  </ul>

  <h2 class="section-heading variations-heading">Variations</h2>
  <ul class="bullet-list variations-list">
    <li>Change the pattern – partner removes something from your original pattern then continues on with the new pattern</li>
  </ul>

  <h2 class="section-heading ideas-heading">Big Ideas</h2>
  <ul class="bullet-list ideas-list">
    <li>Attributes</li>
    <li>Building on a pattern</li>
    <li>Repeat</li>
  </ul>

  <div class="pattern-row pattern-row-first" role="img" aria-label="Row of autumn leaves forming a repeating pattern with one green leaf in the middle"></div>
  <div class="pattern-row pattern-row-second" role="img" aria-label="Row of autumn leaves with two different leaves introduced into the pattern"></div>
</div>
</body>
</html>
```